Lumavento business card

We need a modern business card - With our 4 colors - See web: www.lumavento.dk

I have attached logo and som old business Cards we have - Lets Make the new ones shine...:-) -

Industry/Entity Type

Business

Requirements
Must have
• the logo with lumavento only,

```html
<!DOCTYPE html>
<html lang="da">
<head>
<meta charset="utf-8">
<title>Lumavento – visitkort</title>
<link rel="stylesheet" href="https://fonts.googleapis.com/css2?family=Jost:wght@400&family=Open+Sans:wght@400;600&display=swap">
<style>
  :root {
    --lime: #a6c93a;
    --white: #ffffff;
    --ink: #333333;
    --backdrop: #ecebe8;
    --sans: "Open Sans", sans-serif;
    --geo: "Jost", sans-serif;
  }
  * { margin: 0; padding: 0; box-sizing: border-box; }
  html, body { width: 1200px; height: 900px; overflow: hidden; background: var(--backdrop); }
  .stage { position: relative; width: 1200px; height: 900px; }

  .card { position: absolute; background: var(--white); overflow: hidden; box-shadow: 0 2px 8px rgba(0,0,0,.12); }

  /* Front */
  .card-front { left: 77px; top: 34px; width: 589px; height: 364px; }
  .front-header { position: absolute; left: 0; top: 0; width: 100%; height: 164px; }
  .brand-dot { position: absolute; left: 38px; top: 40px; width: 92px; height: 92px; border-radius: 50%; background: var(--lime); }
  .brand-name { position: absolute; left: 180px; top: 48px; width: 266px; text-align: center; font-family: var(--geo); font-size: 22px; letter-spacing: 2.5px; color: var(--ink); line-height: 28px; }
  .brand-rule { position: absolute; left: 180px; top: 88px; width: 266px; height: 3px; background: var(--lime); }
  .tagline { position: absolute; left: 180px; top: 104px; width: 266px; text-align: center; font-family: var(--sans); font-size: 15px; color: var(--ink); line-height: 20px; }

  .front-panel { position: absolute; left: 0; top: 164px; width: 100%; height: 200px; background: var(--lime); color: var(--white); font-family: var(--sans); }
  .person-name { position: absolute; left: 33px; top: 18px; font-weight: 600; font-size: 21px; line-height: 28px; }
  .person-title { position: absolute; left: 35px; top: 46px; font-size: 14px; line-height: 20px; }
  .contact-list { position: absolute; left: 35px; top: 79px; list-style: none; }
  .contact-list li { display: flex; align-items: center; gap: 9px; height: 24.5px; font-size: 15.5px; }
  .contact-list svg { width: 13px; height: 13px; fill: var(--white); flex: none; }
  .address { position: absolute; left: 32px; top: 156px; font-size: 15.5px; line-height: 22px; white-space: nowrap; }

  /* Back */
  .card-back { left: 388px; top: 505px; width: 567px; height: 352px; }
  .back-band { position: absolute; left: 0; top: 128px; width: 100%; height: 108px; background: var(--lime); color: var(--white); font-family: var(--geo); text-align: center; }
  .back-name { position: absolute; left: 0; top: 24px; width: 100%; font-size: 20px; letter-spacing: 2px; line-height: 26px; }
  .back-rule { position: absolute; left: 110px; top: 55px; width: 347px; height: 4px; background: var(--white); border-radius: 2px; }
  .back-title { position: absolute; left: 0; top: 63px; width: 100%; font-size: 20px; letter-spacing: 2px; line-height: 26px; }
</style>
</head>
<body>
<main class="stage">
  <section class="card card-front">
    <header class="front-header">
      <span class="brand-dot" aria-hidden="true"></span>
      <div class="brand-name">lumavento</div>
      <div class="brand-rule"></div>
      <div class="tagline">Lys og lyd i byen</div>
    </header>
    <div class="front-panel">
      <div class="person-name">Aksel Vinterberg</div>
      <div class="person-title">Salgsdirektor</div>
      <ul class="contact-list">
        <li><svg viewBox="0 0 24 24" aria-hidden="true"><path d="M6.6 10.8a15.1 15.1 0 0 0 6.6 6.6l2.2-2.2a1 1 0 0 1 1-.25 11.4 11.4 0 0 0 3.6.57 1 1 0 0 1 1 1V20a1 1 0 0 1-1 1A17 17 0 0 1 3 4a1 1 0 0 1 1-1h3.5a1 1 0 0 1 1 1c0 1.25.2 2.45.57 3.57a1 1 0 0 1-.25 1z"/></svg>+45 40 12 34 56</li>
        <li><svg viewBox="0 0 24 24" aria-hidden="true"><path d="M2 5h20v14H2z"/><path d="M3 6l9 7 9-7" stroke="var(--lime)" stroke-width="1.6" fill="none"/></svg>av@lumavento.dk</li>
        <li><svg viewBox="0 0 24 24" aria-hidden="true"><circle cx="12" cy="12" r="10"/><path d="M2 12h20M12 2c3 3 3 17 0 20M12 2c-3 3-3 17 0 20" stroke="var(--lime)" stroke-width="1.5" fill="none"/></svg>www.lumavento.dk</li>
      </ul>
      <div class="address">Ellebakken 14 - 3400 Skovbølle -Tlf. 38 20 47 90</div>
    </div>
  </section>

  <section class="card card-back">
    <div class="back-band">
      <div class="back-name">Aksel Vinterberg</div>
      <div class="back-rule"></div>
      <div class="back-title">Salgsdirektør</div>
    </div>
  </section>
</main>
</body>
</html>
```